Stationery Design Project for Nimbora, Chicago

Nimbora, a street parking application which helps car drivers find a street parking spot by offering an ideal path along which to look for parking. This path is calculated by our algorithm based on data (e.g. historical data, baseball games schedule, etc.). Along this path the driver will find a spot and will also save 70% of the search time. Customer we target is reg. between 21 and 45 yo.

We envision something young, fresh, bright and original. Slightly abstract maybe. It should represent the idea and elements of finding street parking in the city, e.g. car(s), parking spot, people, city, etc. (just ideas!).

Logo is attached.

Requirement:
- Business Cards (2 Sided Full Color CMYK)
- Letterhead (1 Sided Full Color CMYK)
- Envelope (1 Sided Full Color CMYK)
- Sticker (1 Sided Full Color CMYK), round with a 2inch diameter.

Reason: We're starting to get more and more designs and need more time to look into all of them. Very exciting!! Thanks to everybody!

Hi all, we're in the process of selecting our favs. Though choices!!! Really good submissions. Will keep you posted and sorry for the delay.

Target Market(s)

Car drivers and owners between 21 and 45

Industry/Entity Type

Parking

Requirements
Must have
• Sticker should be round and include company URL nimbora.com and the new logo which we will attach soon.
Should not have
• Should not be too serious or boring.

```html
<!DOCTYPE html>
<html lang="en">
<head>
<meta charset="utf-8">
<title>Nimbora — Business Card</title>
<link rel="stylesheet" href="https://fonts.googleapis.com/css2?family=Open+Sans:wght@400;600;700&display=swap">
<style>
  :root {
    --backdrop: #dcdcdc;
    --card-white: #ffffff;
    --ink-dark: #2b2b2b;
    --ink-grey: #555555;
    --band-deep: #2a3592;
    --band-light: #29a7e1;
    --curve-shadow: #1a1a1a;
    --text-light: #ffffff;
    --photo-sky: #9aa3ad;
    --photo-ground: #6f747a;
    --mark-blue: #1f56c0;
  }
  html, body {
    margin: 0;
    padding: 0;
    width: 956px;
    height: 1200px;
    overflow: hidden;
    background: var(--backdrop);
  }
  .canvas { display: block; }
  .brand-name {
    font-family: "Open Sans", sans-serif;
    font-weight: 600;
    font-size: 92px;
    fill: var(--ink-dark);
  }
  .person-name {
    font-family: "Open Sans", sans-serif;
    font-weight: 700;
    font-size: 24px;
    fill: var(--ink-grey);
  }
  .person-role { font-size: 19px; }
  .contact {
    font-family: "Open Sans", sans-serif;
    font-weight: 400;
    font-size: 21px;
    fill: var(--text-light);
  }
  .contact-label { font-weight: 700; }
</style>
</head>
<body>
<svg class="canvas" width="956" height="1200" viewBox="0 0 956 1200" xmlns="http://www.w3.org/2000/svg">
  <defs>
    <radialGradient id="band-gradient" cx="0.52" cy="0.55" r="0.6">
      <stop offset="0" stop-color="var(--band-light)"/>
      <stop offset="1" stop-color="var(--band-deep)"/>
    </radialGradient>
    <linearGradient id="photo-gradient" x1="0" y1="0" x2="0" y2="1">
      <stop offset="0" stop-color="var(--photo-sky)"/>
      <stop offset="0.4" stop-color="#8a6a6a"/>
      <stop offset="1" stop-color="var(--photo-ground)"/>
    </linearGradient>
    <clipPath id="front-card-shape"><rect x="79" y="90" width="798" height="455" rx="30"/></clipPath>
    <clipPath id="back-card-shape"><rect x="79" y="630" width="798" height="455" rx="30"/></clipPath>
  </defs>

  <!-- Front card -->
  <g class="card card-front" clip-path="url(#front-card-shape)">
    <rect x="79" y="90" width="798" height="455" fill="var(--card-white)"/>
    <path class="contact-band" d="M79 300 Q478 395 877 300 L877 545 L79 545 Z" fill="url(#band-gradient)"/>
    <path class="band-edge" d="M150 318 Q478 378 806 318 Q478 364 150 318 Z" fill="var(--curve-shadow)" opacity="0.85"/>
    <path d="M79 300 Q478 395 877 300" fill="none" stroke="var(--card-white)" stroke-width="2"/>
  </g>
  <g class="brand-lockup">
    <circle cx="283" cy="205" r="76" fill="var(--mark-blue)"/>
    <text class="brand-name" x="390" y="238">nimbora</text>
  </g>
  <text class="person-name" x="495" y="324" text-anchor="middle">Your Name - <tspan class="person-role">Designation</tspan></text>
  <g class="contact-details">
    <text class="contact" x="478" y="431" text-anchor="end"><tspan class="contact-label">t</tspan> : 123-456-7890</text>
    <text class="contact" x="478" y="467" text-anchor="end"><tspan class="contact-label">c</tspan> : 123-456-7890</text>
    <line x1="495" y1="388" x2="495" y2="488" stroke="var(--text-light)" stroke-width="2"/>
    <text class="contact" x="509" y="437">City Name, Street Name</text>
    <text class="contact" x="509" y="468">State Name, Country Code</text>
    <text class="contact" x="495" y="520" text-anchor="middle"><tspan class="contact-label">e</tspan> : name@website.com  <tspan class="contact-label">w</tspan> : www.website.com</text>
  </g>

  <!-- Back card -->
  <g class="card card-back" clip-path="url(#back-card-shape)">
    <rect x="79" y="630" width="798" height="455" fill="var(--card-white)"/>
    <path class="parking-photo" role="img" aria-label="Photo of a crowded city parking lot full of cars" d="M79 878 Q478 960 877 872 L877 1085 L79 1085 Z" fill="url(#photo-gradient)"/>
  </g>
  <g class="brand-lockup">
    <circle cx="283" cy="745" r="76" fill="var(--mark-blue)"/>
    <text class="brand-name" x="390" y="778">nimbora</text>
  </g>
  <text class="person-name" x="495" y="864" text-anchor="middle">Your Name - <tspan class="person-role">Designation</tspan></text>
</svg>
</body>
</html>
```